July 2022 Industrial Manufacturer Product Expo Mexico City

We manufacture large screws and fastners for large Mining equipment, Trains, large ships, airplanes, wind turbines, and so on. We also do custom work base on the customer needs. No matter the size we can make it.
We have a Expo coming up with companies all over the world. We have to stand out we are a family own business so our customer service will be above and beyond anyone can provide. We do not have a sales force to push our products and services we provide one on one service.
Plus@!! I'm looking for anything that you designers can come up with if it was your company to put on a business card, plus i want to do a 1 or 2 sided pamphlet, and then a website. We make Speciality Bolts for large mining equipment these bolts can be 3 to 4 foot long!!! Plus fasteners, Nuts, washers, any, size, strengths, special materials, we offer more of a ono on one customer service, We are a small company, family own, but can fulfill any type of orders. We can also provide special time lines for emergency orders. "We keep the machines running we here at KRV don't believe in down time" We want to hear any slogan based on our company to stand out.
Thanks i really appreciate all your work and options that we have to pick on. Plus just a thought we could possibly want to entertain a experience Marketing internet help maybe a employment possibility. Thanks

I need 2 cards one in Spanish and English Like the steel back ground maybe send me in some bright red and blue writing Same with the Black cards Please remove the word Military The logo KRV maybe integrate a picture of a Bolt 🔩 Thank you

Still looking for I need 2 cards one in Spanish and English Like the steel back ground maybe send me in some bright red and blue writing Same with the Black cards try bright writing Please remove the word Military The logo KRV maybe integrate a picture of a Bolt 🔩 Plus will need the company to make a brochure and website next Thank you

Target Market(s)

Large Mining, Ship, Train, Green Energy, VELM, and Government equipment. Throughout the World

Industry/Entity Type

We can Custom Manufacture any type of Fastners for Mining equipment, Trains, Ships, Green energy, Governments, or military projects. wind turbines,

Contact Information for Business Card

I attached the name and contact info that's on a card, plus the Company Logo. Would like industrial looking background with Bright Colors that will stand out!! If we can insert somewhere maybe on back that we "Custom Manufacture Any Size or Quantity Fastners for Large Mining Equipment, Trains, Ships, Green Energy Equipment or Government Projects

Font styles to use
Other font styles liked:
• You Pick, has to be bold, colorful standout, Professional looking Beable to read it.

Colors

Designer to choose colors to be used in the design.

Requirements
Must have
• Need in Spanish and English TO STANDOUT FROM THE REST OF THE EXPO!! See Business card details, Rounded corners
Nice to have
• Can i see some of the darker cards with Bright Red and Blue letters I like to see the different type of card material, heavy thickness, plastic, transparent, Metal types, Bright Colors, I saw like Raised letters like on the logo.

```html
<!DOCTYPE html>
<html lang="es">
<head>
<meta charset="utf-8">
<title>KRV Business Cards</title>
<link href="https://fonts.googleapis.com/css2?family=Source+Sans+3:wght@400;600&display=swap" rel="stylesheet">
<style>
  :root {
    --backdrop: #2a2a2a;
    --card-light: #ffffff;
    --card-dark: #000000;
    --brand-blue: #0f63b3;
    --name-blue: #1b8fd3;
    --accent-red: #e8140f;
    --rule-grey: #9a9a9a;
  }
  html, body {
    margin: 0;
    padding: 0;
    width: 1093px;
    height: 1200px;
    overflow: hidden;
    background: var(--backdrop);
    font-family: "Source Sans 3", sans-serif;
  }
  .canvas {
    position: relative;
    width: 1093px;
    height: 1200px;
  }
  .card {
    position: absolute;
    left: 264px;
    width: 580px;
    height: 358px;
    text-align: center;
  }
  .card--front { top: 226px; background: var(--card-light); }
  .card--back { top: 620px; background: var(--card-dark); }

  .brand {
    position: absolute;
    left: 0;
    right: 0;
    display: flex;
    justify-content: center;
    align-items: center;
    gap: 14px;
    font-weight: 600;
    font-size: 86px;
    line-height: 1;
    letter-spacing: 6px;
    color: var(--brand-blue);
  }
  .card--front .brand { top: 56px; }
  .card--back .brand { top: 74px; }
  .brand__mark {
    width: 18px;
    height: 18px;
    border-radius: 50%;
    background: var(--brand-blue);
  }

  .person-name {
    position: absolute;
    top: 188px;
    left: 0;
    right: 0;
    margin: 0;
    font-size: 21px;
    font-weight: 600;
    color: var(--name-blue);
  }
  .rule {
    position: absolute;
    left: 50%;
    width: 74px;
    margin-left: -37px;
    height: 1px;
    background: var(--rule-grey);
  }
  .rule--top { top: 223px; }
  .rule--bottom { top: 284px; }

  .quote-line {
    position: absolute;
    top: 229px;
    left: 0;
    right: 0;
    margin: 0;
    font-size: 18.5px;
    font-weight: 600;
    line-height: 24px;
    color: var(--accent-red);
  }
  .contact-row {
    position: absolute;
    top: 293px;
    left: 0;
    right: 0;
    display: flex;
    justify-content: center;
    align-items: center;
    gap: 4px;
    font-size: 19px;
    font-weight: 600;
    color: var(--accent-red);
  }
  .contact-row .icon { width: 16px; height: 17px; }
  .contact-row .gap { width: 8px; }

  .tagline {
    position: absolute;
    top: 228px;
    left: 0;
    right: 0;
    margin: 0;
    font-size: 18.5px;
    font-weight: 400;
    line-height: 23.5px;
    color: var(--accent-red);
  }
</style>
</head>
<body>
<main class="canvas">
  <section class="card card--front" aria-label="Front of business card">
    <div class="brand"><span class="brand__mark"></span><span>KRV</span></div>
    <h1 class="person-name">Lic. Mariana Ofelia Durán Vega</h1>
    <div class="rule rule--top"></div>
    <p class="quote-line">Cotizaciones en<br>krvtornilleria.ventas@correo.mx</p>
    <div class="rule rule--bottom"></div>
    <div class="contact-row">
      <svg class="icon" viewBox="0 0 16 16" aria-hidden="true">
        <path d="M3 1.5l2.5 0 1 3.5-1.6 1.2c.8 1.8 2.1 3.1 3.9 3.9L10 8.5l3.5 1v2.5c0 .8-.7 1.5-1.5 1.5C6.5 13.5 2.5 9.5 1.5 4 1.5 2.6 2.2 1.5 3 1.5z" fill="var(--name-blue)"/>
        <path d="M9.5 2.5a4 4 0 0 1 4 4M9.5 .5a6 6 0 0 1 6 6" stroke="var(--name-blue)" stroke-width="1.2" fill="none"/>
      </svg>
      <span>5550193847</span>
      <span class="gap"></span>
      <svg class="icon" viewBox="0 0 16 16" aria-hidden="true">
        <rect x="3.5" y="1" width="9" height="14" rx="1.5" fill="none" stroke="var(--name-blue)" stroke-width="1.6"/>
        <circle cx="8" cy="12.5" r="1" fill="var(--name-blue)"/>
      </svg>
      <span>5550172264</span>
    </div>
  </section>

  <section class="card card--back" aria-label="Back of business card">
    <div class="brand"><span class="brand__mark"></span><span>KRV</span></div>
    <p class="tagline">Custom Manufacture Any Size or<br>Quantity Fastners for Large&nbsp; Mining<br>Equipment Trains, Ships, Green Energy<br>Equipment or Government Projects</p>
  </section>
</main>
</body>
</html>
```